Intranet for company management ERP Style

We need a redesign for our Intranet webpage (Images, CSS), we have all the code and functionality ready and a basic design but it is not good looking. In order to meet our company standards this design has to be fully responsive and elegant, also should display the colors of the company: (#F17808 #EDAA64 #F4B947 #F2A900 #292828 #3D3D3D #062953) usually Dark orange colors are the main ones, though we wouldn't mind to see other options or to implement a pair of skins that we could switch easily on the webpage.
Access to the webpage can be granted

Target Market(s)

this webpage is for internal use of the company but could also be sold to external customers in the future, our market is cryptocurrency and BPO

Industry/Entity Type

BPO, Cryptocurrency

Coding

Coded - Design and coding required

Number of Pages Required

1 page

Font styles to use
Other font styles liked:
• Headings: Montserrat Extra Bold, Sub headings: Montserrat, Text: Object Sans

Colors
F0912C
F2A743
F7CA91
FBE8D2
FDF5EE

Requirements
Nice to have
• elegant icons designs and menus

```html
<!DOCTYPE html>
<html lang="en">
<head>
<meta charset="utf-8">
<title>Northwind Hub Intranet – Suggestions</title>
<link href="https://fonts.googleapis.com/css2?family=Roboto:wght@400;500;700&display=swap" rel="stylesheet">
<style>
:root{
  --page:#efefef;
  --orange:#f0912c;
  --orange-dark:#f17808;
  --title:#ee6a3a;
  --link:#1a73e8;
  --cream:#fdf5ee;
  --cream-head:#fbf1e7;
  --white:#ffffff;
  --ink:#1e1e1e;
  --text:#555555;
  --muted:#777777;
  --line:#e6e6e6;
  --online:#2ecc40;
}
*{box-sizing:border-box;margin:0;padding:0}
html,body{width:960px;height:1200px;overflow:hidden;background:var(--page);font-family:'Roboto',sans-serif;color:var(--text)}
.screen{position:absolute;left:74px;width:812px;height:514px;background:var(--cream);overflow:hidden}
.screen--form{top:64px}
.screen--table{top:633px}
.brand{position:absolute;left:0;top:0;width:153px;height:41px;background:var(--cream);display:flex;align-items:center;gap:7px;padding-left:12px}
.brand__dot{width:10px;height:10px;border-radius:50%;background:var(--orange)}
.brand__name{font-size:13px;font-weight:700;color:#3d3d3d}
.topbar{position:absolute;left:153px;top:0;right:0;height:41px;background:var(--white);display:flex;align-items:center;padding:0 12px}
.topbar__tools{display:flex;gap:10px;align-items:center}
.topbar__right{margin-left:auto;display:flex;align-items:center;gap:12px}
.avatar{width:29px;height:29px;border-radius:50%;background:linear-gradient(#6b7c8c,#2d3a46)}
.user{font-size:10px;font-weight:700;color:var(--ink)}
.bell{position:relative}
.bell::after{content:"";position:absolute;right:-1px;top:0;width:5px;height:5px;border-radius:50%;background:var(--online)}
.sidebar{position:absolute;left:0;top:41px;width:153px;bottom:0;background:var(--orange)}
.nav__item{position:absolute;left:0;width:153px;height:36px;display:flex;align-items:center;gap:5px;padding-left:26px;color:var(--white);font-size:11.5px;font-weight:500}
.nav__item svg{width:10px;height:10px;fill:currentColor}
.nav__item--active{background:var(--white);color:var(--orange)}
.sidebar__foot{position:absolute;left:24px;font-size:9px;font-weight:500;color:var(--white);display:flex;align-items:center;gap:4px}
.sidebar__foot svg{width:8px;height:8px;fill:currentColor}
.pagehead{position:absolute;left:153px;top:41px;right:0;height:42px;background:var(--white);padding:6px 12px}
.pagehead__title{font-size:12.5px;color:var(--title);font-weight:400}
.crumbs{font-size:8px;color:var(--muted);margin-top:4px}
.crumbs a{color:var(--link);text-decoration:none;margin-right:4px}
.crumbs span{color:var(--link);margin-right:4px}
.card{position:absolute;left:174px;top:103px;width:620px;background:var(--white);border-radius:5px;overflow:hidden}
.card--form{height:393px}
.card__head{height:31px;background:var(--orange);color:var(--white);font-size:10.5px;font-weight:500;padding:8px 13px}
.field{position:absolute;left:20px;width:581px;height:81px;background:var(--white);box-shadow:0 0 4px rgba(0,0,0,.08);border-radius:3px;padding:12px;font-size:10.5px;color:var(--text)}
.select{position:absolute;left:20px;top:334px;width:308px;height:35px;background:var(--white);box-shadow:0 0 4px rgba(0,0,0,.08);border-radius:3px;padding:11px 12px;font-size:10.5px;display:flex;justify-content:space-between;align-items:center}
.select::after{content:"";border:4px solid transparent;border-top:5px solid var(--ink);margin-top:4px}
.btn-save{position:absolute;left:508px;top:334px;width:93px;height:35px;background:var(--orange);color:var(--white);border-radius:4px;font-size:12px;font-weight:500;display:flex;align-items:center;justify-content:center}
.card--table{height:309px}
.exports{position:absolute;left:14px;top:15px;display:flex;gap:5px}
.exports span{width:55px;height:20px;background:var(--orange);color:var(--white);border-radius:3px;font-size:10px;display:flex;align-items:center;justify-content:center}
.search{position:absolute;left:484px;top:15px;width:125px;height:20px;border:1px solid #ccc;border-radius:3px;font-size:8px;padding:5px 8px;color:var(--text)}
.grid{position:absolute;left:16px;top:51px;width:593px;border-collapse:collapse;font-size:9px;box-shadow:0 0 4px rgba(0,0,0,.06)}
.grid th{height:35px;background:var(--cream-head);font-weight:400;text-align:left;color:var(--text)}
.grid td{height:34px;border-bottom:1px solid var(--line)}
.grid tr:last-child td{border-bottom:none}
.grid th:first-child,.grid td:first-child{padding-left:19px}
.sort::after{content:" ⬍";font-size:8px;color:#333}
.info{position:absolute;left:31px;top:283px;font-size:9px}
.pager{position:absolute;right:17px;top:278px;display:flex;align-items:center;gap:5px;font-size:9px}
.pager b{width:24px;height:18px;background:var(--orange);color:var(--white);border-radius:2px;display:flex;align-items:center;justify-content:center;font-weight:500}
.copyright{position:absolute;left:188px;top:490px;font-size:8.5px}
</style>
</head>
<body>

<svg width="0" height="0" style="position:absolute">
  <symbol id="i-menu" viewBox="0 0 18 14"><rect width="18" height="2"/><rect y="6" width="18" height="2"/><rect y="12" width="18" height="2"/></symbol>
  <symbol id="i-search" viewBox="0 0 18 18"><circle cx="7.5" cy="7.5" r="6" fill="none" stroke="#111" stroke-width="1.6"/><path d="M12 12l5 5" stroke="#111" stroke-width="1.8"/></symbol>
  <symbol id="i-grid" viewBox="0 0 12 12"><rect width="5" height="5"/><rect x="7" width="5" height="5"/><rect y="7" width="5" height="5"/><rect x="7" y="7" width="5" height="5"/></symbol>
  <symbol id="i-mail" viewBox="0 0 20 14"><rect width="20" height="14"/><path d="M0 0l10 8 10-8M0 14l7-6M20 14l-7-6" stroke="#fff" stroke-width="1.4" fill="none"/></symbol>
  <symbol id="i-bell" viewBox="0 0 14 16"><path d="M7 0a5 5 0 0 0-5 5v5L0 13h14l-2-3V5a5 5 0 0 0-5-5zM5 14a2 2 0 0 0 4 0z"/></symbol>
  <symbol id="i-home" viewBox="0 0 10 10"><path d="M5 1a5 5 0 0 0-5 5v2h10V6a5 5 0 0 0-5-5z"/></symbol>
  <symbol id="i-check" viewBox="0 0 10 10"><rect x=".5" y=".5" width="9" height="9" rx="1.5" fill="none" stroke="currentColor" stroke-width="1.2"/><path d="M2.5 5l2 2 4-5" fill="none" stroke="currentColor" stroke-width="1.3"/></symbol>
  <symbol id="i-chart" viewBox="0 0 10 10"><rect x="1" y="5" width="1.5" height="4"/><rect x="3.5" y="2" width="1.5" height="7"/><rect x="6" y="4" width="1.5" height="5"/><rect y="9" width="10" height="1"/></symbol>
  <symbol id="i-share" viewBox="0 0 10 10"><circle cx="2" cy="5" r="2"/><circle cx="8" cy="2" r="2"/><circle cx="8" cy="8" r="2"/><path d="M2 5l6-3M2 5l6 3" stroke="currentColor"/></symbol>
  <symbol id="i-plus" viewBox="0 0 10 10"><rect width="10" height="10" rx="2"/><path d="M5 2v6M2 5h6" stroke="#f0912c" stroke-width="1.5"/></symbol>
  <symbol id="i-spin" viewBox="0 0 10 10"><circle cx="5" cy="1" r="1"/><circle cx="9" cy="5" r="1"/><circle cx="5" cy="9" r="1"/><circle cx="1" cy="5" r="1"/><circle cx="8" cy="2" r=".8"/><circle cx="2" cy="8" r=".8"/><circle cx="2" cy="2" r=".8"/><circle cx="8" cy="8" r=".8"/></symbol>
  <symbol id="i-shield" viewBox="0 0 10 10"><path d="M5 0L1 1.5V5c0 2.5 2 4.3 4 5 2-.7 4-2.5 4-5V1.5z"/></symbol>
  <symbol id="i-gear" viewBox="0 0 10 10"><circle cx="5" cy="5" r="3.5"/><circle cx="5" cy="5" r="1.4" fill="#f0912c"/></symbol>
  <symbol id="i-user" viewBox="0 0 10 10"><circle cx="5" cy="3" r="2.5"/><path d="M0 10a5 4 0 0 1 10 0z"/></symbol>
  <symbol id="i-list" viewBox="0 0 10 10"><rect y="1" width="10" height="8" fill="none" stroke="currentColor"/><path d="M2 4h6M2 6h6" stroke="currentColor"/></symbol>
</svg>

<!-- Add suggestion screen -->
<section class="screen screen--form">
  <div class="brand"><span class="brand__dot"></span><span class="brand__name">Northwind Hub</span></div>
  <header class="topbar">
    <div class="topbar__tools">
      <svg width="17" height="13"><use href="#i-menu"/></svg>
      <svg width="16" height="16"><use href="#i-search"/></svg>
      <svg width="10" height="10"><use href="#i-grid"/></svg>
    </div>
    <div class="topbar__right">
      <svg width="20" height="14"><use href="#i-mail"/></svg>
      <svg class="bell" width="14" height="16"><use href="#i-bell"/></svg>
      <div class="avatar" role="img" aria-label="User profile photo"></div>
      <span class="user">ALEX MORGAN</span>
    </div>
  </header>
  <nav class="sidebar">
    <div class="nav__item" style="top:12px"><svg><use href="#i-home"/></svg>Home</div>
    <div class="nav__item" style="top:54px"><svg><use href="#i-check"/></svg>Requests</div>
    <div class="nav__item" style="top:97px"><svg><use href="#i-chart"/></svg>Reports</div>
    <div class="nav__item" style="top:139px"><svg><use href="#i-share"/></svg>Helpdesk</div>
    <div class="nav__item" style="top:181px"><svg><use href="#i-plus"/></svg>Payroll</div>
    <div class="nav__item nav__item--active" style="top:224px"><svg><use href="#i-spin"/></svg>Suggestion Box</div>
    <div class="nav__item" style="top:266px"><svg><use href="#i-shield"/></svg>Administrator</div>
    <div class="sidebar__foot" style="top:405px"><svg><use href="#i-gear"/></svg>Localhost</div>
    <div class="sidebar__foot" style="top:429px"><svg><use href="#i-user"/></svg>Superlogin</div>
    <div class="sidebar__foot" style="top:453px"><svg><use href="#i-list"/></svg>Dashboard</div>
  </nav>
  <div class="pagehead">
    <h1 class="pagehead__title">Suggestion</h1>
    <p class="crumbs"><a href="#">Home</a><span>&gt;</span>Add New Suggestion</p>
  </div>
  <div class="card card--form">
    <div class="card__head">Add New Suggestion</div>
    <div class="field" style="top:55px">Describe your suggestion*</div>
    <div class="field" style="top:148px">How would your suggestion help us?*</div>
    <div class="field" style="top:242px">Additional Comment</div>
    <div class="select">Select Country</div>
    <div class="btn-save">Save</div>
  </div>
</section>

<!-- Suggestion report screen -->
<section class="screen screen--table">
  <div class="brand"><span class="brand__dot"></span><span class="brand__name">Northwind Hub</span></div>
  <header class="topbar">
    <div class="topbar__tools">
      <svg width="17" height="13"><use href="#i-menu"/></svg>
      <svg width="16" height="16"><use href="#i-search"/></svg>
      <svg width="10" height="10"><use href="#i-grid"/></svg>
    </div>
    <div class="topbar__right">
      <svg width="20" height="14"><use href="#i-mail"/></svg>
      <svg class="bell" width="14" height="16"><use href="#i-bell"/></svg>
      <div class="avatar" role="img" aria-label="User profile photo"></div>
      <span class="user">ALEX MORGAN</span>
    </div>
  </header>
  <nav class="sidebar">
    <div class="nav__item" style="top:12px"><svg><use href="#i-home"/></svg>Home</div>
    <div class="nav__item" style="top:54px"><svg><use href="#i-check"/></svg>Requests</div>
    <div class="nav__item nav__item--active" style="top:96px"><svg><use href="#i-chart"/></svg>Reports</div>
    <div class="nav__item" style="top:139px"><svg><use href="#i-share"/></svg>Helpdesk</div>
    <div class="nav__item" style="top:181px"><svg><use href="#i-plus"/></svg>Payroll</div>
    <div class="nav__item" style="top:224px"><svg><use href="#i-spin"/></svg>Suggestion Box</div>
    <div class="nav__item" style="top:266px"><svg><use href="#i-shield"/></svg>Administrator</div>
    <div class="sidebar__foot" style="top:405px"><svg><use href="#i-gear"/></svg>Localhost</div>
    <div class="sidebar__foot" style="top:429px"><svg><use href="#i-user"/></svg>Superlogin</div>
    <div class="sidebar__foot" style="top:453px"><svg><use href="#i-list"/></svg>Dashboard</div>
  </nav>
  <div class="pagehead">
    <h1 class="pagehead__title">Suggestion</h1>
    <p class="crumbs"><a href="#">Report</a><span>&gt;</span>Suggestion</p>
  </div>
  <div class="card card--table">
    <div class="exports"><span>Copy</span><span>CSV</span><span>Excel</span><span>PDF</span><span>Print</span></div>
    <div class="search">Search:</div>
    <table class="grid">
      <colgroup><col style="width:139px"><col style="width:110px"><col style="width:122px"><col style="width:108px"><col></colgroup>
      <thead><tr><th class="sort">User name</th><th class="sort">Description</th><th class="sort">Suggestion Help</th><th class="sort">Comments</th><th class="sort">Date</th></tr></thead>
      <tbody>
        <tr><td>Super admin</td><td>hola</td><td>hola</td><td>test</td><td>25 Nov 2021 08:48 PM</td></tr>
        <tr><td>Super admin</td><td>hola</td><td>hola</td><td>test</td><td>25 Nov 2021 08:48 PM</td></tr>
        <tr><td>Super admin</td><td>hola</td><td>hola</td><td>test</td><td>25 Nov 2021 08:48 PM</td></tr>
        <tr><td>Super admin</td><td>asdasd</td><td>fasdfasdf</td><td>asdfadfasd</td><td>25 Nov 2021 08:48 PM</td></tr>
        <tr><td>User name</td><td>Description</td><td>Suggestion Help</td><td>Comments</td><td>Date</td></tr>
      </tbody>
    </table>
    <p class="info">Showing 1 to 4 of 4 entries</p>
    <div class="pager"><span>Previous</span><b>1</b><span>Next</span></div>
  </div>
  <p class="copyright">© Copyright | northwind-hub 2022. All Right Reserved</p>
</section>

</body>
</html>
```